Design and Renovation Company Luxury Business Card

I want to create a luxury business card for a Design and Renovation Firm . We will use our current logo. The company name is 528BUILDA. We do not want anything standard. We need a very unique concept.
Please see uploaded inspiration. I really like the textured paper option. I would like the card to be thick with debossing, and/or embossing options. The logo has orange in it but I would like to see the card with and without the orange. I think the orange may make the company feel less high-end. The goal is to elevate the logo not match its vibe per se of the logo. We want something very unique, not standard at all!
I would like a space for :
Logo,
Name,
Position,
Email,
Office number,
Website Address,
Business Address,
Thank you!
Have fun!
Target Market(s)
Home owners Age 35 +
Industry/Entity Type
Design and Renovation
Contact Information for Business Card
Logo, Name, Position, Email, Office number, Website Address, Business Address,.
Colors
Designer to choose colors to be used in the design.
Requirements
Must have
- A luxury designer feel. Must be black or dark grey but open to other luxury ideas.
Nice to have
- Gold, silver, black embossing or debossing. Textured paper design.
Should not have
- A cheap look and feel.

```html
<!DOCTYPE html>
<html lang="en">
<head>
<meta charset="utf-8">
<title>528BUILDA Business Card</title>
<link rel="stylesheet" href="https://fonts.googleapis.com/css2?family=Poppins:wght@300;400;500;600;700&display=swap">
<style>
  :root {
    --page-bg: #dfe5e6;
    --card-bg: #212125;
    --accent: #f7931e;
    --white: #ffffff;
    --soft-white: #e9e9e9;
  }
  * { margin: 0; padding: 0; box-sizing: border-box; }
  html, body {
    width: 1200px; height: 960px; overflow: hidden;
    background: var(--page-bg);
    font-family: "Poppins", sans-serif;
  }
  .canvas { position: relative; width: 1200px; height: 960px; }

  .card {
    position: absolute; left: 252px; width: 700px; height: 400px;
    border-radius: 34px; overflow: hidden;
    background: var(--card-bg);
    border-left: 4px solid var(--accent);
    border-bottom: 4px solid var(--accent);
  }
  .card--back { top: 60px; }
  .card--front { top: 500px; }

  /* back side */
  .back-texture {
    position: absolute; inset: 0;
    background:
      radial-gradient(ellipse at 100% 0%, rgba(235,235,235,0.55) 0%, rgba(150,150,150,0.25) 30%, rgba(33,33,37,0) 65%),
      linear-gradient(160deg, #1e1e22 0%, #111114 100%);
  }
  .back-mark {
    position: absolute; left: 574px; top: 290px; width: 60px;
    display: flex; flex-direction: column; align-items: center; gap: 8px;
  }
  .back-mark .mark-dot { width: 14px; height: 14px; border-radius: 50%; background: var(--white); }
  .back-mark .mark-name {
    font-size: 10px; font-weight: 500; letter-spacing: 0.06em; color: var(--white);
  }

  /* front side */
  .brand-dot {
    position: absolute; left: 40px; top: 44px;
    width: 24px; height: 24px; border-radius: 50%; background: var(--white);
  }
  .brand { position: absolute; left: 90px; top: 28px; }
  .brand-name {
    font-size: 46px; font-weight: 500; line-height: 1.1; letter-spacing: 0.03em; color: var(--white);
  }
  .brand-tagline {
    margin-top: 6px; padding-left: 4px;
    font-size: 11px; font-weight: 600; letter-spacing: 0.32em; color: var(--soft-white);
  }

  .person { position: absolute; right: 30px; top: 26px; text-align: right; }
  .person-name { font-size: 38px; line-height: 1.05; color: var(--white); letter-spacing: 0.01em; }
  .person-name .first { color: var(--accent); font-weight: 700; }
  .person-name .last { font-weight: 300; }
  .person-title { font-size: 18px; font-weight: 500; color: var(--white); letter-spacing: 0.02em; margin-top: 2px; }
  .person-bar {
    position: absolute; right: 0; top: 31px; width: 19px; height: 61px; background: var(--accent);
  }

  .address {
    position: absolute; left: 21px; top: 218px;
    font-style: normal;
    font-size: 19px; line-height: 26px; color: var(--accent); font-weight: 400;
  }
  .contacts { position: absolute; left: 21px; top: 300px; list-style: none; }
  .contacts li {
    display: flex; align-items: center; gap: 14px;
    height: 26px; font-size: 19px; color: var(--white);
  }
  .contacts svg { width: 18px; height: 18px; flex: none; }

  .front-relief {
    position: absolute; left: 449px; top: 140px; width: 251px; height: 260px;
    background:
      linear-gradient(135deg, rgba(90,90,92,0.0) 0%, rgba(90,90,92,0.55) 45%, rgba(33,33,37,0) 46%),
      linear-gradient(180deg, #2a2a2d 0%, #0c0c0e 100%);
  }
</style>
</head>
<body>
<div class="canvas">

  <section class="card card--back">
    <div class="back-texture" role="img" aria-label="Embossed grid of square tiles fading from white at the top right to black"></div>
    <div class="back-mark">
      <span class="mark-dot"></span>
      <span class="mark-name">528BUILDA</span>
    </div>
  </section>

  <section class="card card--front">
    <span class="brand-dot"></span>
    <div class="brand">
      <div class="brand-name">528BUILDA</div>
      <div class="brand-tagline">Design and Renovation Firm</div>
    </div>

    <div class="person">
      <div class="person-name"><span class="first">Marta</span> <span class="last">Kovalik</span></div>
      <div class="person-title">Founder &amp; CEO</div>
    </div>
    <span class="person-bar"></span>

    <address class="address">
      1847 Alder Crest Ave. Suite 310<br>
      Riverton, TX 75990
    </address>

    <ul class="contacts">
      <li>
        <svg viewBox="0 0 24 24" aria-hidden="true"><path fill="#f7931e" d="M6.6 10.8c1.4 2.8 3.8 5.1 6.6 6.6l2.2-2.2c.3-.3.7-.4 1-.2 1.1.4 2.3.6 3.6.6.6 0 1 .4 1 1V20c0 .6-.4 1-1 1C10.6 21 3 13.4 3 4c0-.6.4-1 1-1h3.5c.6 0 1 .4 1 1 0 1.3.2 2.5.6 3.6.1.3 0 .7-.2 1z"/></svg>
        (555) 214-7730
      </li>
      <li>
        <svg viewBox="0 0 24 24" aria-hidden="true"><circle cx="12" cy="12" r="9" fill="none" stroke="#f7931e" stroke-width="2"/><ellipse cx="12" cy="12" rx="4" ry="9" fill="none" stroke="#f7931e" stroke-width="1.6"/><line x1="3" y1="12" x2="21" y2="12" stroke="#f7931e" stroke-width="1.6"/></svg>
        info@yourwebsite.com
      </li>
      <li>
        <svg viewBox="0 0 24 24" aria-hidden="true"><rect x="3" y="6" width="18" height="13" rx="1" fill="none" stroke="#f7931e" stroke-width="2"/><path d="M3 7l9 7 9-7" fill="none" stroke="#f7931e" stroke-width="2"/></svg>
        www.yourwebsite.com
      </li>
    </ul>

    <div class="front-relief" role="img" aria-label="Large embossed dark square tiles in the lower right corner"></div>
  </section>

</div>
</body>
</html>
```